creation of a business card design for a company specializing in the creation...

I would like to create a design for a professional business card on a black background and with the company's colors (I am attaching some files: including the logo in horizontal and centered format, I am also attaching a recent project design a T-shirt, this is the one I chose to give you an idea of my preferences.

we are in the process of developing a new website design, it is still in the development phase but it can be viewed at the following address: www.vantrelmo.be to give you other ideas about the company
you will see for yourself the subject of my main activity: company specializing in the construction of stairs

I would like a business card that stands out from the rest with a unique design

here is the informations
Name: Lucien Barthel
Function: Manager
Address: Rue Moulinet du Parc 42
7180 La Louvière
telephone: +32 468 219 804
email: info@rx7p.be
website: rx7p. be
social networks: Facebook, YouTube, TikTok, Instagram

Target Market(s)

customer who wants to have a beautiful staircase built

Industry/Entity Type

contruction d'escalier

Contact Information for Business Card

Adresse. Numero de telephone, site web, le texte : "Createur d'escalier", logo recto-verso, icone des reseaux sociaux

Requirements
Must have
• the mention: Stair creator
Nice to have
• an illustration of a designer staircase
Should not have
• do not distort the logo

```html
<!DOCTYPE html>
<html lang="fr">
<head>
<meta charset="utf-8">
<title>RX7P – Cartes de visite</title>
<link href="https://fonts.googleapis.com/css2?family=Open+Sans:wght@400;600;700&display=swap" rel="stylesheet">
<style>
  :root {
    --canvas: #e4e1dc;
    --card: #0f0f10;
    --card-edge: #1c1d1f;
    --steel: #5f8dab;
    --steel-dark: #2f5a73;
    --steel-light: #a9cbe0;
    --ink: #f2f4f6;
    --muted: #9fb3c1;
  }
  * { margin: 0; padding: 0; box-sizing: border-box; }
  html, body { width: 1200px; height: 780px; overflow: hidden; }
  body {
    background: var(--canvas);
    font-family: "Open Sans", Arial, sans-serif;
    display: flex;
    align-items: center;
    justify-content: center;
    gap: 60px;
  }
  .card {
    position: relative;
    width: 520px;
    height: 336px;
    background: radial-gradient(ellipse at 30% 25%, var(--card-edge), var(--card) 70%);
    border-radius: 4px;
    overflow: hidden;
    box-shadow: 0 10px 28px rgba(0,0,0,.28);
    color: var(--ink);
  }

  /* brand mark stand-in */
  .brand {
    position: absolute;
    display: flex;
    flex-direction: column;
    align-items: center;
    text-align: center;
  }
  .brand-row { display: flex; align-items: center; gap: 10px; }
  .brand-dot { border-radius: 50%; background: var(--steel); }
  .brand-name { font-weight: 700; color: var(--ink); letter-spacing: .04em; }
  .brand-tagline { font-weight: 600; color: var(--steel-light); text-transform: uppercase; letter-spacing: .12em; }
  .brand-contact { color: var(--muted); letter-spacing: .06em; }

  /* front */
  .front .brand { left: 40px; top: 58px; width: 200px; }
  .front .brand-dot { width: 26px; height: 26px; }
  .front .brand-name { font-size: 34px; }
  .front .brand-tagline { font-size: 10px; margin-top: 8px; }
  .front .brand-contact { font-size: 8px; margin-top: 6px; }

  .divider { position: absolute; left: 210px; top: 40px; }

  .person { position: absolute; left: 292px; top: 92px; }
  .person-name { font-size: 27px; font-weight: 700; color: var(--steel); line-height: 1.1; }
  .person-role { font-size: 15px; margin-top: 2px; }
  .contacts { list-style: none; margin-top: 18px; }
  .contacts li { display: flex; align-items: center; gap: 8px; font-size: 14px; line-height: 1.55; }
  .contacts svg { width: 12px; height: 12px; fill: var(--steel); flex: none; }

  .address-band {
    position: absolute;
    left: 0; bottom: 0;
    width: 100%; height: 40px;
    background: linear-gradient(90deg, var(--steel-dark), var(--steel) 70%, var(--steel-light));
    display: flex; align-items: center;
    padding-left: 34px;
    font-size: 14px;
  }
  .band-block {
    position: absolute;
    right: 36px; bottom: 24px;
    width: 44px; height: 44px;
    background: var(--steel-light);
  }

  /* back */
  .back .brand { left: 0; right: 0; top: 78px; }
  .back .brand-dot { width: 40px; height: 40px; }
  .back .brand-name { font-size: 58px; }
  .back .brand-tagline { font-size: 15px; margin-top: 12px; }
  .back .brand-contact { font-size: 11px; margin-top: 10px; }
</style>
</head>
<body>

  <article class="card front">
    <div class="brand">
      <div class="brand-row">
        <span class="brand-dot"></span>
        <span class="brand-name">RX7P</span>
      </div>
      <span class="brand-tagline">Créateur d'escalier</span>
      <span class="brand-contact">0468 219 804 · rx7p.be</span>
    </div>

    <svg class="divider" width="70" height="210" viewBox="0 0 70 210">
      <line x1="68" y1="2" x2="2" y2="208" stroke="#cfd6dc" stroke-width="1"/>
    </svg>

    <div class="person">
      <h1 class="person-name">Lucien Barthel</h1>
      <p class="person-role">Manager</p>
      <ul class="contacts">
        <li><svg viewBox="0 0 24 24"><path d="M6.6 10.8a15.1 15.1 0 0 0 6.6 6.6l2.2-2.2a1 1 0 0 1 1-.25 11.4 11.4 0 0 0 3.6.6 1 1 0 0 1 1 1V20a1 1 0 0 1-1 1A17 17 0 0 1 3 4a1 1 0 0 1 1-1h3.5a1 1 0 0 1 1 1c0 1.25.2 2.45.6 3.6a1 1 0 0 1-.25 1z"/></svg>+32 468 219 804</li>
        <li><svg viewBox="0 0 24 24"><path d="M2 5h20v14H2z M3 6l9 7 9-7" fill="none" stroke="#5f8dab" stroke-width="2"/></svg>info@rx7p.be</li>
        <li><svg viewBox="0 0 24 24"><circle cx="12" cy="12" r="10"/></svg>www.vantrelmo.be</li>
      </ul>
    </div>

    <div class="address-band">Rue Moulinet du Parc 42 7180 La Louvière</div>
    <span class="band-block"></span>
  </article>

  <article class="card back">
    <div class="brand">
      <div class="brand-row">
        <span class="brand-dot"></span>
        <span class="brand-name">RX7P</span>
      </div>
      <span class="brand-tagline">Créateur d'escalier</span>
      <span class="brand-contact">0468 219 804 · rx7p.be</span>
    </div>
  </article>

</body>
</html>
```